Lorvex Tilo medical cannibis cultivation company

tag - Tilo rise
Lorvex Tilo medical cannabis cultivation - logo is selected- can we please see bold examples with our selection. We are mainly dealing with medical companies and professionals. We would like to be stand out in the crowd with our designs. Welcome any and all attempts. Thanks

Target Market(s)

Medical and Professional

Industry/Entity Type

Medical And Science

Font styles to use
Sans Serif

Colors

Designer to choose colors to be used in the design.

Requirements
Must have
• Bright colour and be bold- Love the teal and magenta that is currently on the dark background design.
Nice to have
• shading and the 3D affect- The shadowed appearance.
Should not have
• Anything related to illegal activity or un professional manners

```html
<!DOCTYPE html>
<html lang="en">
<head>
<meta charset="utf-8">
<title>Lorvex Tilo Stationery</title>
<link rel="stylesheet" href="https://fonts.googleapis.com/css2?family=Questrial&family=Roboto:wght@400;500&display=swap">
<style>
  :root {
    --backdrop: #dcdcdc;
    --paper: #f6f6f6;
    --teal: #14ace4;
    --magenta: #a04d9c;
    --ink: #444444;
    --ink-soft: #5a5a5a;
    --flap: #050505;
    --grey-ring: #8a8a8a;
  }
  * { margin: 0; padding: 0; box-sizing: border-box; }
  html, body { width: 1200px; height: 877px; overflow: hidden; background: var(--backdrop); }
  body { position: relative; font-family: "Questrial", sans-serif; color: var(--ink); }

  .sheet {
    position: absolute;
    background: var(--paper);
    box-shadow: 0 1px 4px rgba(0,0,0,0.18);
    overflow: hidden;
  }
  .letterhead { left: 60px; top: 66px; width: 528px; height: 741px; }
  .envelope-back { left: 615px; top: 299px; width: 531px; height: 240px; }
  .envelope-front { left: 616px; top: 568px; width: 531px; height: 238px; }

  .brand { position: absolute; text-align: center; }
  .brand-dot {
    display: block; margin: 0 auto 5px;
    width: 50px; height: 50px; border-radius: 50%;
    border: 2px solid var(--grey-ring);
  }
  .brand-name {
    display: block;
    font-family: "Questrial", sans-serif;
    font-size: 17px; letter-spacing: 0.5px;
    color: var(--teal); white-space: nowrap;
  }
  .brand-tag {
    display: block; margin-top: 1px;
    font-family: "Questrial", sans-serif;
    font-size: 6.5px; letter-spacing: 1.2px;
    color: var(--teal); white-space: nowrap;
  }
  .letterhead .brand { left: 0; right: 0; top: 44px; }

  .watermark {
    position: absolute;
    background: radial-gradient(ellipse at center, rgba(160,77,156,0.10), rgba(20,172,228,0.05) 55%, rgba(246,246,246,0) 75%);
  }
  .letterhead .watermark { left: 230px; top: 380px; width: 300px; height: 380px; }
  .envelope-front .watermark { left: 340px; top: 0; width: 200px; height: 200px; }

  .letter { position: absolute; left: 47px; top: 273px; width: 440px; }
  .salutation { font-size: 13.5px; color: var(--ink); margin-bottom: 26px; }
  .letter p {
    font-size: 7.7px; line-height: 11.45px; color: var(--ink-soft);
    text-align: justify; margin-bottom: 11.5px;
  }
  .closing { font-size: 7.7px; color: var(--ink-soft); margin-top: 20px; }
  .signature { width: 94px; height: 40px; margin-top: 17px;
    background: linear-gradient(90deg, rgba(30,70,160,0.18), rgba(30,70,160,0.06)); border-radius: 4px; }

  .footer { position: absolute; left: 0; bottom: 0; width: 100%; height: 50px; }
  .footer svg { position: absolute; left: 0; top: 0; width: 100%; height: 50px; }
  .footer-text {
    position: absolute; left: 0; right: 0; top: 20px;
    font-family: "Roboto", sans-serif; font-size: 8.8px; line-height: 11.5px;
    text-align: center; color: #ffffff;
  }
  .footer-text b { font-weight: 500; }
  .envelope-front .footer-text { color: rgba(255,255,255,0.75); }

  .flap { position: absolute; left: 0; top: 0; width: 531px; height: 74px; }
  .flap-mark {
    position: absolute; left: 258px; top: 31px;
    width: 14px; height: 14px; border-radius: 50%; background: var(--teal);
  }

  .envelope-front .brand { left: 30px; top: 28px; }
</style>
</head>
<body>

  <section class="sheet letterhead">
    <div class="watermark" role="img" aria-label="Faint oversized leaf motif in soft magenta and teal"></div>
    <div class="brand">
      <span class="brand-dot"></span>
      <span class="brand-name">Lorvex Tilo</span>
      <span class="brand-tag">TILO RISE</span>
    </div>

    <div class="letter">
      <div class="salutation">Dear Mr. Harlow,</div>
      <p>Lorem ipsum dolor sit amet, consectetur adipiscing elit. Donec orci purus, luctus vitae dignissim eu, iaculis sed purus. Vivamus faucibus, ipsum nec aliquet viverra, leo mauris condimentum ligula, sit amet sagittis enim ligula quis arcu. Nam egestas tortor id nisi porttitor mattis. In tortor ante, ultricies in suscipit a, tempus non massa. Vivamus et auctor mi. Fusce vel massa nulla. Phasellus nec eros mauris, et scelerisque orci.</p>
      <p>Donec malesuada orci vitae nulla accumsan porta a id massa. Quisque accumsan iaculis magna sit amet fringilla. Maecenas consequat, magna eget tincidunt semper, odio nibh rutrum mi, id feugiat ante nisi eu risus. Vestibulum nunc orci, rhoncus a placerat in, ultricies in mi. Cras mattis varius eros, vel fringilla nisi suscipit eget. Quisque scelerisque sagittis nulla at porttitor.</p>
      <p>Sed id augue vitae urna euismod commodo aliquet a quam. Pellentesque arcu velit, cursus et malesuada ut, consequat et diam. Nullam erat sem, rhoncus id ullamcorper vitae, rhoncus et arcu. In ultricies ultricies nulla, ut rutrum nisi iaculis at. Donec eu magna a metus ornare faucibus. Fusce aliquet faucibus ultricies. Morbi semper, est id tincidunt gravida, sem arcu adipiscing lacus, ac bibendum nulla leo eu purus. Quisque nec diam sed risus consectetur a ccumsan quis quis nibh. Vestibulum id purus lorem.</p>
      <p>It is a long established fact that a reader will be distracted by the readable content of a page when looking at its layout. The point of using Lorem Ipsum is that it has a more-or-less normal distribution of letters, as opposed to using 'Content here, content here', making it look like readable English. Many desktop publishing packages</p>
      <div class="closing">Sincerely,</div>
      <div class="signature" role="img" aria-label="Handwritten signature of Evan Harlow in blue ink"></div>
    </div>

    <footer class="footer">
      <svg viewBox="0 0 528 50" preserveAspectRatio="none" aria-hidden="true">
        <path d="M0 19 Q264 -6 528 19 L528 50 L0 50 Z" fill="var(--magenta)"/>
        <path d="M0 17 Q264 -8 528 17" fill="none" stroke="var(--teal)" stroke-width="3"/>
      </svg>
      <div class="footer-text">
        4120 Fernwick Road, Maple Bay, Oregon 90418 &nbsp;|&nbsp; <b>P:</b> 555 201 4417<br>
        <b>C:</b> 555 308 7720 <b>F:</b> 555 612 0953 <b>E:</b> evan@lorvextilo.com &nbsp;<b>W:</b> www.lorvextilo.com
      </div>
    </footer>
  </section>

  <section class="sheet envelope-back">
    <svg class="flap" viewBox="0 0 531 74" aria-hidden="true">
      <path d="M0 0 L531 0 L531 4 Q528 40 516 62 Q510 74 492 74 L40 74 Q22 74 16 62 Q4 40 0 4 Z" fill="var(--flap)"/>
    </svg>
    <span class="flap-mark"></span>
  </section>

  <section class="sheet envelope-front">
    <div class="watermark" role="img" aria-label="Faint leaf motif in soft magenta and teal"></div>
    <div class="brand">
      <span class="brand-dot"></span>
      <span class="brand-name">Lorvex Tilo</span>
      <span class="brand-tag">TILO RISE</span>
    </div>
    <footer class="footer">
      <svg viewBox="0 0 531 50" preserveAspectRatio="none" aria-hidden="true">
        <path d="M0 19 Q265 -6 531 19 L531 50 L0 50 Z" fill="var(--magenta)"/>
        <path d="M0 17 Q265 -8 531 17" fill="none" stroke="var(--teal)" stroke-width="3"/>
      </svg>
      <div class="footer-text">
        4120 Fernwick Road, Maple Bay, Oregon 90418 &nbsp;|&nbsp; <b>P:</b> 555 201 4417<br>
        <b>C:</b> 555 308 7720 <b>F:</b> 555 612 0953 <b>E:</b> evan@lorvextilo.com &nbsp;<b>W:</b> www.lorvextilo.com
      </div>
    </footer>
  </section>

</body>
</html>
```